Year End Gift for Employees

Looking for assistance in creating an album cover. Here are some ideas that I have: Double Platinum, Lantern Crow Drifting, 2025 World Tour
QT/QR (name of the band) – on the front of the album cover
List of Songs - on the back of the album cover
Would like to have the ability to have team / individual pictures on the inside of the double platinum album cover
DON’T want anything gory or vulgar for the album cover
Also want rights to the image for the album cover to use for t-shirts
This is a Sales Team that work within Home Improvement Industries
Any additional images that you want to propose, I'm open too. Thanks and I'll await your response
Colleagues

```html
<!DOCTYPE html>
<html lang="en">
<head>
<meta charset="utf-8">
<title>QT/QR 2025 World Tour – Disc Label</title>
<link rel="stylesheet" href="https://fonts.googleapis.com/css2?family=Pirata+One&family=Mrs+Saint+Delafield&display=swap">
<style>
  :root {
    --page-bg: #ffffff;
    --steel-light: #d9e0ea;
    --steel-mid: #a9b7c9;
    --steel-deep: #7f93ab;
    --steel-shade: #6d819b;
    --emboss-dark: #2e3f5c;
    --emboss-light: #eef2f7;
    --letter-face: #9fb0c4;
    --script-ink: #0b0b0d;
  }
  html, body {
    margin: 0;
    padding: 0;
    width: 1200px;
    height: 1200px;
    overflow: hidden;
    background: var(--page-bg);
  }
  .disc-label {
    display: block;
    width: 1200px;
    height: 1200px;
  }
  .band-name {
    font-family: "Pirata One", "UnifrakturCook", fantasy;
    font-size: 330px;
  }
  .band-name .shadow { fill: var(--emboss-dark); opacity: 0.75; }
  .band-name .highlight { fill: var(--emboss-light); opacity: 0.7; }
  .band-name .face { fill: var(--letter-face); }
  .tour-script {
    font-family: "Mrs Saint Delafield", cursive;
    fill: var(--script-ink);
  }
</style>
</head>
<body>
<svg class="disc-label" viewBox="0 0 1200 1200" xmlns="http://www.w3.org/2000/svg" role="img" aria-label="QT/QR 2025 World Tour disc label">
  <defs>
    <linearGradient id="steel-sheen" x1="0" y1="0" x2="1" y2="1">
      <stop offset="0" stop-color="var(--steel-deep)"/>
      <stop offset="0.35" stop-color="var(--steel-mid)"/>
      <stop offset="0.55" stop-color="var(--steel-light)"/>
      <stop offset="0.75" stop-color="var(--steel-mid)"/>
      <stop offset="1" stop-color="var(--steel-shade)"/>
    </linearGradient>
    <radialGradient id="center-glow" cx="0.6" cy="0.5" r="0.45">
      <stop offset="0" stop-color="#ffffff" stop-opacity="0.45"/>
      <stop offset="1" stop-color="#ffffff" stop-opacity="0"/>
    </radialGradient>
    <clipPath id="disc-clip"><circle cx="600" cy="600" r="468"/></clipPath>
  </defs>

  <g class="disc" clip-path="url(#disc-clip)">
    <rect class="disc-metal" x="132" y="132" width="936" height="936" fill="url(#steel-sheen)" role="img" aria-label="Brushed steel surface"/>
    <rect x="132" y="132" width="936" height="936" fill="url(#center-glow)"/>

    <g class="band-name">
      <g class="row-top">
        <text class="shadow" x="259" y="520" textLength="675" lengthAdjust="spacingAndGlyphs">QT/QR</text>
        <text class="highlight" x="255" y="516" textLength="675" lengthAdjust="spacingAndGlyphs">QT/QR</text>
        <text class="face" x="257" y="518" textLength="675" lengthAdjust="spacingAndGlyphs">QT/QR</text>
      </g>
      <g class="row-bottom">
        <text class="shadow" x="259" y="930" textLength="675" lengthAdjust="spacingAndGlyphs">QT/QR</text>
        <text class="highlight" x="255" y="926" textLength="675" lengthAdjust="spacingAndGlyphs">QT/QR</text>
        <text class="face" x="257" y="928" textLength="675" lengthAdjust="spacingAndGlyphs">QT/QR</text>
      </g>
    </g>

    <g class="tour-script">
      <text x="787" y="592" font-size="60" textLength="135" lengthAdjust="spacingAndGlyphs">2025</text>
      <text x="688" y="642" font-size="64" textLength="342" lengthAdjust="spacingAndGlyphs">World Tour</text>
    </g>
  </g>

  <circle class="spindle-hole" cx="600" cy="600" r="78" fill="var(--page-bg)"/>
</svg>
</body>
</html>
```